Tall Fern Roofing Business Card

Need a business card with the logo that was designed here

Contact Information for Business Card

Name, Title, Phone, Email, Website, Company name

```html
<!DOCTYPE html>
<html lang="en">
<head>
<meta charset="utf-8">
<title>Tall Fern Roofing – Business Card</title>
<link href="https://fonts.googleapis.com/css2?family=Open+Sans:wght@400;600;700&display=swap" rel="stylesheet">
<style>
  :root {
    --stage: #242426;
    --card: #1c1d20;
    --card-edge: #2a2b2f;
    --pattern-dark: #18191b;
    --pattern-light: #3a3b3f;
    --brand-blue: #1a7bd0;
    --brand-grey: #a7a9ad;
    --ink: #ffffff;
  }
  * { box-sizing: border-box; margin: 0; padding: 0; }
  html, body {
    width: 1200px; height: 780px; overflow: hidden;
    background: var(--stage);
    font-family: "Open Sans", Arial, sans-serif;
  }
  .stage {
    width: 1200px; height: 780px;
    display: flex; align-items: center; justify-content: center; gap: 40px;
  }
  .card {
    position: relative;
    width: 540px; height: 309px;
    background: var(--card);
    border-radius: 4px;
    box-shadow: 0 14px 30px rgba(0,0,0,.55), inset 0 0 0 1px var(--card-edge);
    overflow: hidden;
  }
  /* back side */
  .card-back .roof-pattern {
    position: absolute; inset: 0;
    background: linear-gradient(200deg, var(--pattern-light) 0%, var(--pattern-dark) 45%, var(--pattern-dark) 100%);
  }
  .card-back .brand-name {
    position: absolute; right: 44px; bottom: 70px;
    font-weight: 700; font-size: 20px; color: var(--brand-blue);
    display: flex; align-items: center; gap: 8px;
  }
  .brand-mark {
    width: 12px; height: 12px; background: var(--brand-blue);
  }
  /* front side */
  .card-front .brand-name {
    position: absolute; left: 40px; top: 38px;
    font-weight: 700; font-size: 24px; color: var(--brand-blue);
    display: flex; align-items: center; gap: 10px;
  }
  .card-front .brand-mark { width: 14px; height: 14px; }
  .identity {
    position: absolute; left: 40px; top: 110px;
    padding-left: 18px;
    border-left: 8px solid var(--brand-blue);
  }
  .person-name { font-size: 28px; font-weight: 700; line-height: 1.05; }
  .person-name .first { color: var(--brand-blue); }
  .person-name .last { color: var(--brand-grey); }
  .person-title { color: var(--ink); font-weight: 600; font-size: 13px; margin-top: 2px; }
  .address {
    position: absolute; left: 66px; top: 182px;
    color: var(--ink); font-size: 13px; line-height: 1.35;
  }
  .contact {
    position: absolute; left: 66px; top: 228px;
    list-style: none; color: var(--ink); font-size: 13px; line-height: 1.45;
  }
  .contact li { display: flex; align-items: center; gap: 8px; }
  .contact svg { width: 13px; height: 13px; fill: var(--brand-blue); flex: none; }
</style>
</head>
<body>
<main class="stage">
  <section class="card card-back" aria-label="Business card back">
    <div class="roof-pattern" role="img" aria-label="Repeating roofline pattern in dark glossy tones"></div>
    <div class="brand-name"><span class="brand-mark"></span>Tall Fern Roofing</div>
  </section>

  <section class="card card-front" aria-label="Business card front">
    <div class="brand-name"><span class="brand-mark"></span>Tall Fern Roofing</div>
    <div class="identity">
      <p class="person-name"><span class="first">Dana</span> <span class="last">Whitlow</span></p>
      <p class="person-title">Managing Director</p>
    </div>
    <p class="address">1840 Cedar Ridge Ln. Suite 310<br>Milford, TX 76670</p>
    <ul class="contact">
      <li>
        <svg viewBox="0 0 24 24" aria-hidden="true"><path d="M6.6 10.8a15.1 15.1 0 0 0 6.6 6.6l2.2-2.2a1 1 0 0 1 1-.25 11.4 11.4 0 0 0 3.6.57 1 1 0 0 1 1 1V20a1 1 0 0 1-1 1A17 17 0 0 1 3 4a1 1 0 0 1 1-1h3.5a1 1 0 0 1 1 1c0 1.25.2 2.45.57 3.57a1 1 0 0 1-.25 1z"/></svg>
        (555) 214-6730
      </li>
      <li>
        <svg viewBox="0 0 24 24" aria-hidden="true"><path d="M3 5h18a1 1 0 0 1 1 1v12a1 1 0 0 1-1 1H3a1 1 0 0 1-1-1V6a1 1 0 0 1 1-1zm9 7.5L4 7.2V8l8 5.3L20 8v-.8z"/></svg>
        info@tallfernroofing.com
      </li>
      <li>
        <svg viewBox="0 0 24 24" aria-hidden="true"><path d="M12 2a10 10 0 1 0 0 20 10 10 0 0 0 0-20zm6.9 6h-3a15.6 15.6 0 0 0-1.4-3.6A8 8 0 0 1 18.9 8zM12 4a14 14 0 0 1 1.9 4h-3.8A14 14 0 0 1 12 4zM4.3 14a8.2 8.2 0 0 1 0-4h3.4a16.5 16.5 0 0 0 0 4zm.8 2h3a15.6 15.6 0 0 0 1.4 3.6A8 8 0 0 1 5.1 16zm3-8h-3a8 8 0 0 1 4.4-3.6A15.6 15.6 0 0 0 8.1 8zM12 20a14 14 0 0 1-1.9-4h3.8A14 14 0 0 1 12 20zm2.3-6H9.7a14.7 14.7 0 0 1 0-4h4.6a14.7 14.7 0 0 1 0 4zm.2 5.6a15.6 15.6 0 0 0 1.4-3.6h3a8 8 0 0 1-4.4 3.6zm1.8-5.6a16.5 16.5 0 0 0 0-4h3.4a8.2 8.2 0 0 1 0 4z"/></svg>
        www.tallfernroofing.com
      </li>
    </ul>
  </section>
</main>
</body>
</html>
```